Business Card Design Project

We are a construction company in Orange County, CA. We need a two sided business card. We would like the back to be our logo with web URL. Front should included Name, title, address, phone, fax and email address.

our address is
627 West Dorrance Blvd, Suite 308
Anaheim, CA 92718

Our logo files are attached.

Construction

```html
<!DOCTYPE html>
<html lang="en">
<head>
<meta charset="utf-8">
<title>Braxton Business Card</title>
<link rel="stylesheet" href="https://fonts.googleapis.com/css2?family=Source+Sans+3:wght@400;600;700;800&display=swap">
<style>
  :root {
    --navy: #174a7e;
    --paper: #ffffff;
    --ink: #333333;
    --backdrop: #e9e7e3;
    --edge: #b9b5ae;
  }
  * { margin: 0; padding: 0; box-sizing: border-box; }
  html, body {
    width: 1200px; height: 1033px; overflow: hidden;
    background: var(--backdrop);
    font-family: "Source Sans 3", Arial, sans-serif;
  }
  .stage { position: relative; width: 1200px; height: 1033px; }

  .card { position: absolute; width: 738px; height: 422px; overflow: hidden; }
  .card-front {
    left: 73px; top: 70px;
    background: var(--paper);
    border: 1px solid var(--edge);
  }
  .card-back {
    left: 378px; top: 534px;
    background: var(--navy);
  }

  .band { position: absolute; left: 98px; width: 543px; height: 15px; background: var(--navy); }
  .band-top { top: 0; border-radius: 0 0 15px 15px; }
  .band-bottom { bottom: 0; border-radius: 15px 15px 0 0; }

  .brand-name {
    position: absolute; left: 0; width: 100%;
    text-align: center;
    font-weight: 700; font-size: 90px; line-height: 1;
    letter-spacing: 3px;
  }
  .card-front .brand-name { top: 52px; color: var(--navy); }
  .card-back .brand-name { top: 140px; color: var(--paper); }

  .contact {
    position: absolute; left: 0; top: 236px; width: 100%;
    text-align: center; color: var(--ink);
  }
  .person { color: var(--navy); font-size: 26px; line-height: 1; margin-bottom: 22px; }
  .person-name { font-weight: 700; }
  .person-title { font-weight: 400; }
  .contact-row {
    display: flex; justify-content: center; align-items: center; gap: 8px;
    font-size: 18px; line-height: 24px;
  }
  .contact-item { display: inline-flex; align-items: center; gap: 5px; }
  .contact-item svg { width: 14px; height: 14px; fill: var(--ink); }
  .contact-item svg.icon-globe { fill: none; stroke: var(--ink); stroke-width: 1.4; }
  .address { font-size: 18px; margin-top: 18px; }

  .web-url {
    position: absolute; left: 0; top: 290px; width: 100%;
    text-align: center; color: var(--paper);
    font-size: 20px; letter-spacing: 3.5px;
  }
</style>
</head>
<body>
<main class="stage">
  <section class="card card-front" aria-label="Card front">
    <div class="band band-top"></div>
    <div class="brand-name">BRAXTON</div>
    <div class="contact">
      <p class="person"><span class="person-name">Your Name,</span> <span class="person-title">Title</span></p>
      <div class="contact-row">
        <span class="contact-item">
          <svg viewBox="0 0 16 16" aria-label="Phone"><path d="M3.5 1.5l2.5 2.8-1.4 1.9c.9 2 2.6 3.7 4.6 4.6l1.9-1.4 2.8 2.5-1.6 2.2C7 13.9 2.1 9 1.3 3.1z"/></svg>01-234-5678
        </span>
        <span class="contact-item">
          <svg viewBox="0 0 16 16" aria-label="Fax"><path d="M4 1h8v4H4zM1 6h14v7h-2v-2H3v2H1zM4 12h8v3H4z"/></svg>01-234-5678
        </span>
      </div>
      <div class="contact-row">
        <span class="contact-item">
          <svg viewBox="0 0 16 16" aria-label="Email"><path d="M1 3h14v10H1zM2 4.2v.6l6 4 6-4v-.6z"/></svg>info@braxtonbuild.com
        </span>
        <span class="contact-item">
          <svg class="icon-globe" viewBox="0 0 16 16" aria-label="Website"><circle cx="8" cy="8" r="6.3"/><ellipse cx="8" cy="8" rx="2.8" ry="6.3"/><path d="M1.7 8h12.6"/></svg>www.braxtonbuild.com
        </span>
      </div>
      <p class="address">627 West Dorrance Blvd, Suite 308, Anaheim, CA&nbsp; 92718</p>
    </div>
    <div class="band band-bottom"></div>
  </section>

  <section class="card card-back" aria-label="Card back">
    <div class="brand-name">BRAXTON</div>
    <p class="web-url">www.braxtonbuild.com</p>
  </section>
</main>
</body>
</html>
```